Ward Compass Business Card Design*

We need a business card design for our company Ward Compass. Our company is specialized in providing online consulting services regarding medical institutions, hospitals and doctors. We work with patients worldwide looking to choose between healthcare providers. We have a website you may use as a reference, where we list doctors and clinics worldwide. So we target Medical providers as well as patients worldwide.
Target Market(s)
Medical Providers and patients around the world
Industry/Entity Type
Medical
Contact Information for Business Card
Salwa Kettani
CEO
+90 612 348 2175
info@wardcompass.example
www.wardcompass.example
14 Annakhil 7 H.R.B. Rabat, Morocco
Requirements
Must have
- Company logo/name on one full side, personal info and smaller logo and company name on the other side.
Nice to have
- Smart and elegant design

```html
<!DOCTYPE html>
<html lang="en">
<head>
<meta charset="utf-8">
<title>Ward Compass Business Card</title>
<link rel="stylesheet" href="https://fonts.googleapis.com/css2?family=Arimo:wght@400;700&display=swap">
<style>
  :root {
    --backdrop: #d9d2c8;
    --card-top: #eef0f2;
    --card-mid: #d4dae0;
    --navy: #1d2a40;
    --navy-deep: #0f1726;
    --swoosh: #5a5858;
    --silver: #e9e9ea;
    --brand-ink: #27324a;
    --name-ink: #e8e9ee;
    --role-ink: #a9adb6;
    --contact-ink: #d2bfbf;
    --web-ink: #a89f96;
  }
  html, body {
    margin: 0;
    width: 1200px;
    height: 970px;
    overflow: hidden;
    background: var(--backdrop);
    font-family: "Arimo", Arial, sans-serif;
  }
  .card {
    position: absolute;
    left: 80px;
    top: 187px;
    width: 1040px;
    height: 595px;
    border-radius: 30px;
    overflow: hidden;
    background: linear-gradient(160deg, var(--card-top) 0%, var(--card-mid) 100%);
    box-shadow: 0 18px 40px rgba(40, 30, 20, 0.25);
  }
  .card-waves {
    position: absolute;
    inset: 0;
  }
  .brand {
    position: absolute;
    left: 65px;
    top: 105px;
    display: flex;
    align-items: center;
    gap: 26px;
  }
  .brand-dot {
    width: 92px;
    height: 92px;
    border-radius: 50%;
    background: var(--brand-ink);
  }
  .brand-name {
    font-size: 44px;
    font-weight: 700;
    letter-spacing: 1px;
    color: var(--brand-ink);
    text-transform: uppercase;
  }
  .person {
    position: absolute;
    left: 65px;
    top: 392px;
  }
  .person-name {
    margin: 0;
    font-size: 31px;
    font-weight: 400;
    color: var(--name-ink);
    letter-spacing: 0.5px;
  }
  .person-name strong { font-weight: 700; }
  .person-role {
    margin: 6px 0 0;
    font-size: 23px;
    color: var(--role-ink);
  }
  .contacts {
    position: absolute;
    left: 68px;
    top: 484px;
    margin: 0;
    padding: 0;
    list-style: none;
    font-size: 23px;
    color: var(--contact-ink);
  }
  .contacts li {
    display: flex;
    align-items: center;
    gap: 14px;
    height: 33px;
  }
  .contacts svg { width: 20px; height: 20px; fill: none; stroke: var(--role-ink); stroke-width: 2; }
  .website {
    position: absolute;
    right: 58px;
    top: 518px;
    font-size: 22px;
    color: var(--web-ink);
  }
</style>
</head>
<body>
  <div class="card">
    <svg class="card-waves" viewBox="0 0 1040 595" width="1040" height="595" aria-hidden="true">
      <defs>
        <linearGradient id="navyFill" x1="0" y1="0" x2="0.3" y2="1">
          <stop offset="0" stop-color="#2b3a55"/>
          <stop offset="0.6" stop-color="var(--navy)"/>
          <stop offset="1" stop-color="var(--navy-deep)"/>
        </linearGradient>
        <linearGradient id="swooshFill" x1="0" y1="0" x2="1" y2="0">
          <stop offset="0" stop-color="#6c6a69"/>
          <stop offset="0.5" stop-color="#8a8886"/>
          <stop offset="1" stop-color="var(--swoosh)"/>
        </linearGradient>
      </defs>
      <path d="M0,332 C240,300 450,322 620,340 C820,362 960,300 1040,180 L1040,362 C880,382 700,372 520,362 C320,350 150,356 0,372 Z" fill="url(#swooshFill)"/>
      <path d="M0,364 C180,344 380,346 560,362 C760,380 930,376 1040,356 L1040,368 C930,388 760,392 560,374 C380,358 180,356 0,378 Z" fill="var(--silver)"/>
      <path d="M0,378 C180,356 380,358 560,374 C760,392 930,388 1040,368 L1040,595 L0,595 Z" fill="url(#navyFill)"/>
    </svg>

    <div class="brand">
      <span class="brand-dot"></span>
      <span class="brand-name">Ward Compass</span>
    </div>

    <div class="person">
      <h1 class="person-name"><strong>SALWA</strong> KETTANI</h1>
      <p class="person-role">CEO</p>
    </div>

    <ul class="contacts">
      <li>
        <svg viewBox="0 0 20 20"><rect x="5" y="2" width="10" height="16" rx="1.5"/><line x1="9" y1="15" x2="11" y2="15"/></svg>
        <span>+90 612 348 2175</span>
      </li>
      <li>
        <svg viewBox="0 0 20 20"><rect x="2" y="5" width="16" height="11"/><polyline points="2,5 10,11 18,5"/></svg>
        <span>info@wardcompass.example</span>
      </li>
    </ul>

    <div class="website">www.wardcompass.example</div>
  </div>
</body>
</html>
```